Business Card Design - VNT (company name)

Over 20 years of progressive technology design, migration and management experience that drives business objectives and streamlines operations. Continuously challenge conventions to meet and exceed business security, availability and functionality requirements. Maintain exceptional vendor relationships to ensure ongoing knowledge of emerging products and to secure preferred service agreements. Recruit and utilize top talent and foster a collegial environment that advances innovation and performance excellence. design logo using 3 arrows of different colors green, gold, blue

Industry/Entity Type

Progressive

Contact Information for Business Card

Martin K. Osgood
IT Strategist / Consultant

626.583.2907 MOsgood@vntosgood.example 4817 Brenning Court Pasadena, CA 91104

Colors
0255a3
f37122
fece3e

Requirements
Must have
• Note NEW EMAIL ADDRESS
• MOsgood@vntosgood.example
• NOTE NEW ORDER of the work I do.
• Infrastructure – Systems – Cybersecurity
Nice to have
• main color should be orange

```html
<!DOCTYPE html>
<html lang="en">
<head>
<meta charset="utf-8">
<title>VNT Business Card</title>
<link href="https://fonts.googleapis.com/css2?family=Lato:wght@400;700&display=swap" rel="stylesheet">
<style>
  :root {
    --stage: #d6d6d4;
    --card: #0b0b0b;
    --card-edge: #1a1a1a;
    --text: #ffffff;
    --title-blue: #1f74c9;
    --icon-blue: #1b6fc2;
    --mark-square: #f37122;
  }
  * { box-sizing: border-box; margin: 0; padding: 0; }
  html, body {
    width: 1200px;
    height: 900px;
    overflow: hidden;
    background: var(--stage);
    font-family: "Lato", sans-serif;
  }
  .stage {
    width: 1200px;
    height: 900px;
    display: flex;
    flex-direction: column;
    align-items: center;
    justify-content: center;
    gap: 40px;
  }
  .card {
    position: relative;
    width: 680px;
    height: 389px;
    background: var(--card);
    border: 1px solid var(--card-edge);
    color: var(--text);
  }
  /* Back of card */
  .card-back .brand {
    position: absolute;
    left: 0;
    right: 0;
    top: 120px;
    display: flex;
    justify-content: center;
    align-items: center;
    gap: 14px;
  }
  .brand-square {
    width: 22px;
    height: 22px;
    background: var(--mark-square);
  }
  .brand-name {
    font-weight: 700;
    font-size: 64px;
    letter-spacing: 4px;
    color: var(--text);
    line-height: 1;
  }
  .services {
    position: absolute;
    left: 0;
    right: 0;
    top: 248px;
    text-align: center;
    font-size: 16px;
    letter-spacing: 0.3px;
    word-spacing: 1px;
  }
  .services .sep { margin: 0 7px; }
  /* Front of card */
  .card-front .brand {
    position: absolute;
    left: 70px;
    top: 92px;
    display: flex;
    align-items: center;
    gap: 12px;
  }
  .card-front .brand-name { font-size: 58px; }
  .contact {
    position: absolute;
    right: 44px;
    top: 170px;
    text-align: right;
  }
  .contact-name {
    font-weight: 700;
    font-size: 27px;
    line-height: 1.1;
  }
  .contact-role {
    color: var(--title-blue);
    font-size: 18px;
    margin-top: 2px;
  }
  .contact-lines {
    list-style: none;
    margin-top: 20px;
    font-size: 17px;
  }
  .contact-lines li {
    display: flex;
    justify-content: flex-end;
    align-items: center;
    gap: 10px;
    line-height: 27px;
  }
  .icon {
    width: 20px;
    height: 20px;
    flex: none;
  }
  .address {
    margin-top: 10px;
    font-size: 17px;
    line-height: 22px;
    padding-right: 30px;
  }
</style>
</head>
<body>
<main class="stage">
  <section class="card card-back">
    <div class="brand">
      <span class="brand-square"></span>
      <span class="brand-name">VNT</span>
    </div>
    <p class="services">IT Strategist<span class="sep">|</span>ConsultantSystems<span class="sep">|</span>Infrastructure<span class="sep">|</span>Cybersecurity</p>
  </section>

  <section class="card card-front">
    <div class="brand">
      <span class="brand-square"></span>
      <span class="brand-name">VNT</span>
    </div>
    <div class="contact">
      <h1 class="contact-name">Martin K. Osgood</h1>
      <p class="contact-role">Managing Director</p>
      <ul class="contact-lines">
        <li>626.583.2907
          <svg class="icon" viewBox="0 0 20 20" aria-hidden="true">
            <rect width="20" height="20" rx="3" fill="var(--icon-blue)"/>
            <rect x="6.5" y="3.5" width="7" height="13" rx="1.5" fill="none" stroke="#fff" stroke-width="1.4"/>
            <circle cx="10" cy="14" r="0.9" fill="#fff"/>
          </svg>
        </li>
        <li>MOsgood@vntosgood.example
          <svg class="icon" viewBox="0 0 20 20" aria-hidden="true">
            <rect width="20" height="20" rx="3" fill="var(--icon-blue)"/>
            <rect x="4" y="6" width="12" height="8.5" fill="#fff"/>
            <path d="M4 6 L10 11 L16 6" fill="none" stroke="var(--icon-blue)" stroke-width="1.2"/>
          </svg>
        </li>
      </ul>
      <p class="address">4817 Brenning Court<br>Pasadena, CA 91104</p>
    </div>
  </section>
</main>
</body>
</html>
```